Up to the Challenge - PPT Template with Splash Slide

We are looking for a PPT template that has 4 slides.
1. Splash slide (Creative, fun, no content, a visual representation of the theme)
2. Section header slide
3. Content Slide
4. Content Slide, another design option
The theme is 'UP to the Challenge'. The design should reflect this theme.
The colors should be in Purple (#864B99), Blue (#0A80C2), and Green (#52B054).

```html
<!DOCTYPE html>
<html lang="en">
<head>
<meta charset="utf-8">
<title>Up to the Challenge – Presentation Template</title>
<link href="https://fonts.googleapis.com/css2?family=Montserrat:wght@500;700;800&family=Roboto:wght@300;400&display=swap" rel="stylesheet">
<style>
  :root{
    --canvas:#3a3a3a;
    --purple:#864b99;
    --blue:#0a80c2;
    --green:#52b054;
    --teal:#1cbfb0;
    --navy:#1e4e6e;
    --ink:#111;
    --text:#333;
    --muted:#8a8a8a;
    --white:#fff;
    --sky:#bfd9ea;
    --lavender:#e6dcef;
  }
  *{box-sizing:border-box;margin:0;padding:0}
  html,body{width:1033px;height:1200px;overflow:hidden;background:var(--canvas)}
  body{position:relative;font-family:'Roboto',Arial,sans-serif;color:var(--text)}
  .slide{position:absolute;width:460px;height:258px;overflow:hidden;background:var(--white)}
  .col-left{left:48px}.col-right{left:525px;width:459px}
  .row-1{top:43px}.row-2{top:327px}.row-3{top:611px}.row-4{top:895px}
  .abs{position:absolute}
  .company{position:absolute;font-family:'Montserrat',Arial,sans-serif;font-weight:700;font-size:10.5px;color:var(--ink)}
  .company.light{color:var(--white)}
  .heading{font-family:'Montserrat',Arial,sans-serif;font-weight:800;letter-spacing:.2px}
  .photo{position:absolute}
  .body-copy{font-family:'Montserrat',Arial,sans-serif;font-weight:500;font-size:5.6px;line-height:9.1px;text-align:justify;color:#444}

  /* slide 1 */
  .s1 .photo{inset:0;background:linear-gradient(180deg,#3f9aa0 0%,#9cc8bd 35%,#e8d9a8 62%,#e4b878 78%,#1a1410 100%)}
  .s1 .center{position:absolute;left:0;right:0;text-align:center;color:var(--white)}
  .s1 .date{top:178px;font-size:8.5px;font-weight:300}
  .s1 .title{top:200px;font-size:15px}
  .s1 .sub{top:223px;font-size:7.2px;font-weight:300}

  /* slide 2 */
  .s2 .photo{inset:0;background:linear-gradient(90deg,#8a8a8a 0%,#c9c9c9 45%,#e2c7a6 60%,#d6d6d6 78%,#9a9a9a 100%)}
  .s2 .date{left:23px;top:93px;background:var(--white);font-size:9px;font-weight:300;color:#222;padding:1px 4px}
  .s2 .title{left:23px;top:118px;font-size:14.5px;color:var(--ink)}
  .s2 .sub{left:23px;top:143px;background:var(--white);font-size:7.2px;font-weight:300;color:#222;padding:1px 2px}

  /* slide 3 */
  .s3{background:linear-gradient(135deg,#f7f7f7 0%,#ececec 40%,#f8f8f8 60%,#eaeaea 100%)}
  .s3 .band{position:absolute;left:0;right:0;top:64px;height:123px;background:var(--purple);text-align:center;color:var(--white)}
  .s3 .band .heading{margin-top:39px;font-size:18.5px}
  .s3 .band .sub{margin-top:8px;font-size:8.5px;font-weight:300}

  /* slide 4 */
  .s4{background:var(--sky)}
  .s4 .photo{right:0;top:0;width:230px;height:258px;background:radial-gradient(ellipse at 60% 60%,#3f8ee8 0%,#7fb4ec 35%,var(--sky) 70%)}
  .s4 .heading{position:absolute;left:28px;top:102px;font-size:22px;color:var(--blue)}
  .s4 .sub{position:absolute;left:28px;top:137px;font-size:8.5px;line-height:14.5px;font-weight:300;color:#333}

  /* slide 5 */
  .s5 .column{position:absolute;top:46px;width:193px}
  .s5 .column .heading{font-size:11px;color:var(--blue)}
  .s5 .column .sub{font-size:7.3px;font-weight:300;color:#333;margin-top:4px;padding-bottom:5px;border-bottom:1px solid var(--navy)}
  .s5 .column .body-copy{margin-top:9px}

  /* slide 6 */
  .s6 .strip{position:absolute;left:231px;top:0;width:7px;height:100%;background:var(--lavender)}
  .s6 .panel{position:absolute;left:238px;top:0;right:0;height:100%;background:var(--green)}
  .s6 .heading{position:absolute;left:21px;top:51px;font-size:11px;color:var(--navy)}
  .s6 .body-copy{position:absolute;left:20px;top:76px;width:196px}
  .s6 .bullets{position:absolute;left:254px;top:44px;list-style:none;color:var(--white);font-family:'Montserrat',Arial,sans-serif;font-weight:500;font-size:5.6px;line-height:12px}
  .s6 .bullets li::before{content:"";display:inline-block;width:0;height:0;border-left:2.5px solid var(--white);border-top:2px solid transparent;border-bottom:2px solid transparent;margin:0 6px 0 -8px;vertical-align:middle}
  .s6 .bullets li{padding-left:8px}

  /* slide 7 */
  .s7 .frame{position:absolute;left:182px;top:31px;width:47px;height:224px;border:3px solid var(--purple);border-left:none}
  .s7 .photo{left:14px;top:38px;width:209px;height:210px;background:linear-gradient(180deg,#d9e4ee 0%,#8ba8c8 40%,#35557f 70%,#0f1a2a 100%)}
  .s7 .heading{position:absolute;left:246px;top:51px;font-size:11px;color:var(--blue)}
  .s7 .body-copy{position:absolute;left:246px;top:74px;width:186px}

  /* slide 8 */
  .s8 .heading{position:absolute;left:0;right:0;top:49px;text-align:center;font-size:11px;color:var(--blue)}
  .s8 svg{position:absolute;left:0;top:0}
  .step{position:absolute;top:130px;width:100px;text-align:center}
  .step .icon{height:18px}
  .step .label{font-family:'Montserrat',Arial,sans-serif;font-weight:800;font-size:10px;margin-top:2px}
  .step p{font-family:'Montserrat',Arial,sans-serif;font-weight:500;font-size:3.9px;line-height:6px;letter-spacing:.2px;color:var(--muted);margin-top:3px}
  .step-1{left:28px}.step-1 .label{color:#7b3fe4}
  .step-2{left:177px}.step-2 .label{color:var(--teal)}
  .step-3{left:326px}.step-3 .label{color:#e8384f}
</style>
</head>
<body>

<section class="slide s1 col-left row-1">
  <div class="photo" role="img" aria-label="Person on a mountain peak holding up a target against a sunrise sky"></div>
  <div class="company light" style="left:17px;top:18px">Company Name</div>
  <div class="center date">June 13, 2024</div>
  <div class="center title heading">PRESENTATION TITLE</div>
  <div class="center sub">Lorem Ipsum is simply dummy text of the printing</div>
</section>

<section class="slide s2 col-right row-1">
  <div class="photo" role="img" aria-label="Businessman climbing a stairway toward a glowing city skyline"></div>
  <div class="company light" style="left:23px;top:65px">Company Name</div>
  <div class="abs date">June 13, 2024</div>
  <div class="abs title heading">PRESENTATION TITLE</div>
  <div class="abs sub">Lorem Ipsum is simply dummy text of the printing</div>
</section>

<section class="slide s3 col-left row-2">
  <div class="company" style="left:21px;top:23px">Company Name</div>
  <div class="band">
    <div class="heading">HEADING</div>
    <div class="sub">Lorem Ipsum is simply dummy text of the printing</div>
  </div>
</section>

<section class="slide s4 col-right row-2">
  <div class="photo" role="img" aria-label="Businessman walking up a winding blue staircase"></div>
  <div class="company" style="left:22px;top:18px">Company Name</div>
  <div class="heading">HEADING</div>
  <div class="sub">Lorem Ipsum is simply dummy<br>text of the printing</div>
</section>

<section class="slide s5 col-left row-3">
  <div class="company" style="left:22px;top:14px">Company Name</div>
  <div class="column" style="left:22px">
    <div class="heading">HEADING</div>
    <div class="sub">Lorem Ipsum is simply dummy text of the printing</div>
    <p class="body-copy">Sed ut perspiciatis unde omnis iste natus error sit voluptatem accusantium doloremque laudantium, totam rem aperiam, eaque ipsa quae ab illo inventore veritatis et quasi architecto beatae vitae dicta sunt explicabo. Nemo enim ipsam voluptatem quia voluptas sit aspernatur aut odit aut fugit, sed quia consequuntur magni dolores eos qui ratione voluptatem sequi nesciunt. Neque porro quisquam est, qui dolorem ipsum quia dolor sit amet, consectetur, adipisci velit, sed quia non numquam eius modi tempora incidunt ut labore et dolore magnam aliquam quaerat voluptatem. Ut enim ad minima veniam, quis nostrum exercitationem ullam corporis suscipit laboriosam, nisi ut aliquid ex ea commodi consequatur? Quis autem vel eum iure reprehenderit qui in ea voluptate velit esse quam nihil molestiae consequatur, vel illum qui dolorem eum fugiat quo volu Et harum quidem rerum facilis est et expedita distinctio. Nam libero tempore, cum soluta nobis est eligendi optio cumque nihil impedit quo minus id quod maxime.</p>
  </div>
  <div class="column" style="left:239px">
    <div class="heading">HEADING</div>
    <div class="sub">Lorem Ipsum is simply dummy text of the printing</div>
    <p class="body-copy">Lorem ipsum dolor sit amet, consectetur adipiscing elit, sed do eiusmod tempor incididunt ut labore et dolore magna aliqua. Ut enim ad minim veniam, quis nostrud exercitation ullamco laboris nisi ut aliquip ex ea commodo consequat. Duis aute irure dolor in reprehenderit in voluptate velit esse cillum dolore eu fugiat nulla pariatur. Excepteur sint occaecat cupidatat non proident, sunt in culpa qui officia deserunt mollit anim id est laborum Nemo enim ipsam voluptatem quia voluptas sit aspernatur aut odit aut fugit, sed quia consequuntur magni dolores eos qui ratione voluptatem sequi nesciunt. Neque porro quisquam est, qui dolorem ipsum quia dolor sit amet, consectetur, adipisci velit, sed quia non numquam eius modi tempora incidunt ut labore et dolore magnam aliquam quaerat voluptatem. Ut enim ad minima veniam, quis nostrum exercitationem ullam corporis suscipit laboriosam, nisi ut aliquid ex ea commodi consequatur? Quis autem vel eum iure reprehenderit qui in ea voluptate velit esse quam nihil molestiae consequatur, vel</p>
  </div>
</section>

<section class="slide s6 col-right row-3">
  <div class="company" style="left:20px;top:18px">Company Name</div>
  <div class="heading">HEADING</div>
  <p class="body-copy">Sed ut perspiciatis unde omnis iste natus error sit voluptatem accusantium doloremque laudantium, totam rem aperiam, eaque ipsa quae ab illo inventore veritatis et quasi architecto beatae vitae dicta sunt explicabo. Nemo enim ipsam voluptatem quia voluptas sit aspernatur aut odit aut fugit, sed quia consequuntur magni dolores eos qui ratione voluptatem sequi nesciunt. Neque porro quisquam est, qui dolorem ipsum quia dolor sit amet, consectetur, adipisci velit, sed quia non numquam eius modi tempora incidunt ut labore et dolore magnam aliquam quaerat voluptatem. Ut enim ad minima veniam, quis nostrum exercitationem ullam corporis suscipit laboriosam, nisi ut aliquid ex ea commodi consequatur? Quis autem vel eum iure reprehenderit qui in ea voluptate velit esse quam nihil molestiae consequatur, vel illum qui dolorem eum fugiat quo volu Et harum quidem rerum facilis est et expedita distinctio. Nam libero tempore, cum soluta nobis est eligendi optio cumque nihil impedit quo minus id quod maxime.</p>
  <div class="strip"></div>
  <div class="panel"></div>
  <ul class="bullets">
    <li>Lorem ipsum dolor sit amet, consectetur adipiscing elit.</li>
    <li>Quisque vitae dolor vel urna aliquet consectetur at at neque.</li>
    <li>Curabitur euismod tellus sit amet interdum lobortis.</li>
    <li>Etiam id augue ut odio condimentum lobortis.</li>
    <li>Nunc tincidunt enim sed nulla porta, sit amet porta</li>
    <li>Donec sagittis mi et massa aliquet elementum.</li>
    <li>Mauris luctus arcu ut nisl auctor, in blandit lorem blandit.</li>
    <li>Praesent sed enim a turpis pulvinar volutpat ut at turpis.</li>
    <li>Lorem ipsum dolor sit amet, consectetur adipiscing elit.</li>
    <li>Quisque vitae dolor vel urna aliquet consectetur at at neque.</li>
    <li>Curabitur euismod tellus sit amet interdum lobortis.</li>
    <li>Etiam id augue ut odio condimentum lobortis.</li>
    <li>Nunc tincidunt enim sed nulla porta, sit amet porta</li>
    <li>Donec sagittis mi et massa aliquet elementum.</li>
    <li>Mauris luctus arcu ut nisl auctor, in blandit lorem blandit.</li>
    <li>Praesent sed enim a turpis pulvinar volutpat ut at turpis.</li>
  </ul>
</section>

<section class="slide s7 col-left row-4">
  <div class="company" style="left:16px;top:13px">Company Name</div>
  <div class="frame"></div>
  <div class="photo" role="img" aria-label="Silhouette of a climber with raised arms on a misty mountain summit"></div>
  <div class="heading">HEADING</div>
  <p class="body-copy">Sed ut perspiciatis unde omnis iste natus error sit voluptatem accusantium doloremque laudantium, totam rem aperiam, eaque ipsa quae ab illo inventore veritatis et quasi architecto beatae vitae dicta sunt explicabo. Nemo enim ipsam voluptatem quia voluptas sit aspernatur aut odit aut fugit, sed quia consequuntur magni dolores eos qui ratione voluptatem sequi nesciunt. Neque porro quisquam est, qui dolorem ipsum quia dolor sit amet, consectetur, adipisci velit, sed quia non numquam eius modi tempora incidunt ut labore et dolore magnam aliquam quaerat voluptatem. Ut enim ad minima veniam, quis nostrum exercitationem ullam corporis suscipit laboriosam, nisi ut aliquid ex ea commodi consequatur? Quis autem vel eum iure reprehenderit qui in ea voluptate velit esse quam nihil molestiae consequatur, vel illum qui dolorem eum fugiat quo volu Et harum quidem rerum facilis est et expedita distinctio. Nam libero tempore, cum soluta nobis est eligendi optio cumque nihil impedit quo minus id quod maxime.</p>
</section>

<section class="slide s8 col-right row-4">
  <div class="company" style="left:16px;top:14px">Company Name</div>
  <div class="heading">HEADING</div>
  <svg width="459" height="258" viewBox="0 0 459 258" aria-hidden="true">
    <defs>
      <filter id="soft" x="-30%" y="-30%" width="160%" height="160%">
        <feDropShadow dx="0" dy="1" stdDeviation="3" flood-color="#000" flood-opacity=".12"/>
      </filter>
      <linearGradient id="blueTeal" x1="0" x2="1"><stop offset="0" stop-color="#0a80c2"/><stop offset="1" stop-color="#1cbfb0"/></linearGradient>
      <linearGradient id="greenPurple" x1="0" x2="1"><stop offset="0" stop-color="#52b054"/><stop offset="1" stop-color="#864b99"/></linearGradient>
    </defs>
    <circle cx="78" cy="159" r="56" fill="#fff" filter="url(#soft)"/>
    <circle cx="227" cy="159" r="56" fill="#fff" filter="url(#soft)"/>
    <circle cx="376" cy="159" r="56" fill="#fff" filter="url(#soft)"/>
    <g fill="none" stroke-width="2.4" stroke-linecap="round">
      <path d="M123 108 A64 64 0 1 0 128 199" stroke="#0a80c2"/>
      <path d="M128 199 C150 175 165 100 227 95" stroke="url(#blueTeal)"/>
      <path d="M227 95 A64 64 0 0 1 285 126" stroke="#1cbfb0"/>
      <path d="M164 185 A64 64 0 0 0 277 199" stroke="#52b054"/>
      <path d="M277 199 C300 175 314 100 376 95" stroke="url(#greenPurple)"/>
      <path d="M376 95 A64 64 0 1 1 328 207" stroke="#864b99"/>
    </g>
    <circle cx="123" cy="108" r="4" fill="#5d5bd4"/>
    <circle cx="285" cy="126" r="4" fill="#1cbfb0"/>
    <circle cx="164" cy="185" r="4" fill="#1cbfb0"/>
    <circle cx="328" cy="207" r="4" fill="#9b6b7b"/>
  </svg>
  <div class="step step-1">
    <svg class="icon" width="14" height="18" viewBox="0 0 14 18"><path d="M7 1a5.5 5.5 0 0 0-3 10.1V13h6v-1.9A5.5 5.5 0 0 0 7 1z" fill="#8a3ff0"/><rect x="4.5" y="14" width="5" height="1.4" rx=".7" fill="#8a3ff0"/><rect x="5.2" y="16" width="3.6" height="1.4" rx=".7" fill="#8a3ff0"/></svg>
    <div class="label">Step 01</div>
    <p>Lorem ipsum dolor sit amet, consectetur adipiscing elit. Fusce dignissim pretium consectetur. Curabitur tempor posuere massa in varius. Pellentesque viverra nibh</p>
  </div>
  <div class="step step-2">
    <svg class="icon" width="16" height="18" viewBox="0 0 16 18"><rect x="1" y="4" width="14" height="10" fill="none" stroke="#1cbfb0" stroke-width="1.2"/><path d="M1 4l7 6 7-6M1 14l5-5M15 14l-5-5" fill="none" stroke="#1cbfb0" stroke-width="1.2"/></svg>
    <div class="label">Step 02</div>
    <p>Lorem ipsum dolor sit amet, consectetur adipiscing elit. Fusce dignissim pretium consectetur. Curabitur tempor posuere massa in varius. Pellentesque viverra nibh</p>
  </div>
  <div class="step step-3">
    <svg class="icon" width="16" height="18" viewBox="0 0 16 18"><path d="M1.5 2v14h14" fill="none" stroke="#e8384f" stroke-width="1.3"/><path d="M3.5 13l4-5 3 3 4-6" fill="none" stroke="#e8384f" stroke-width="1.3"/><path d="M11.5 5h3v3" fill="none" stroke="#e8384f" stroke-width="1.3"/></svg>
    <div class="label">Step 03</div>
    <p>Lorem ipsum dolor sit amet, consectetur adipiscing elit. Fusce dignissim pretium consectetur. Curabitur tempor posuere massa in varius. Pellentesque viverra nibh</p>
  </div>
</section>

</body>
</html>
```